Garland Custom Boats Website update

I would like an updated website to my current site (Garlandboats.com).
I have an updated logo i would like to incorporate.
24 pages , would like to integrate videos of the boats (that i can upload later)

Target Market(s)

Professional and Commercial boat owners

Industry/Entity Type

Custom Boat Manufacturing

Coding

Coded - Design and coding required

Number of Pages Required

5+ page

Font styles to use
Serif

Requirements
Must have
• Easy to read, well laid-out, and video integration
Nice to have
• Fresh up to date look

```html
<!DOCTYPE html>
<html lang="en">
<head>
<meta charset="utf-8">
<title>Garland Custom Boats</title>
<link rel="stylesheet" href="https://fonts.googleapis.com/css2?family=Oswald:wght@400;500;600&family=Montserrat:wght@400;500;600&display=swap">
<style>
:root{
  --blue:#1f56b3;
  --blue-deep:#163f8f;
  --red:#c4232b;
  --ink:#1c1c1c;
  --grey:#666;
  --dark:#2b2c2f;
  --white:#fff;
}
*{margin:0;padding:0;box-sizing:border-box}
html,body{width:1200px;height:4504px;overflow:hidden;background:var(--white)}
body{font-family:"Montserrat",sans-serif;color:var(--ink)}
.page{position:relative;width:1200px;height:4504px;overflow:hidden}
.abs{position:absolute}
.heading{font-family:"Oswald",sans-serif;font-weight:500;text-transform:uppercase;color:var(--ink);text-align:center;width:100%;font-size:42px;letter-spacing:.5px}
.btn{position:absolute;background:var(--red);color:var(--white);border-radius:20px;font-size:11px;font-weight:500;display:flex;align-items:center;justify-content:center;text-transform:uppercase;letter-spacing:.3px}
/* nav */
.brand{left:72px;top:44px;font-family:"Oswald",sans-serif;font-weight:600;font-size:30px;color:var(--blue);letter-spacing:1px;line-height:1}
.brand-sub{display:block;font-size:11px;letter-spacing:2px;margin-top:4px}
.nav{left:375px;top:53px;display:flex;gap:0;font-family:"Oswald",sans-serif;font-size:13px;font-weight:500}
.nav span{position:absolute;white-space:nowrap}
/* hero */
.hero-photo{left:0;top:120px;width:1200px;height:570px;background:linear-gradient(160deg,#6e9cc8 0%,#2c5d98 40%,#1d4b85 70%,#9fc0dc 100%)}
.hero-circle{left:100px;top:161px;width:378px;height:378px;border-radius:50%;background:rgba(31,86,179,.92)}
.hero-title{left:100px;top:255px;width:385px;text-align:center;font-family:"Oswald",sans-serif;font-weight:500;font-size:40px;line-height:48px;color:var(--white)}
.hero-text{left:140px;top:360px;width:310px;text-align:center;font-size:15px;line-height:18px;color:var(--white)}
/* features */
.feature{position:absolute;top:870px;width:290px;text-align:center}
.feature svg{display:block;margin:0 auto}
.feature h3{font-family:"Oswald",sans-serif;font-weight:500;font-size:26px;line-height:32px;margin-top:28px}
.feature p{font-size:11.5px;line-height:14px;color:var(--grey);margin-top:12px}
/* inventory */
.card{position:absolute;top:1319px;width:248px;height:277px}
.card .shot{position:absolute;inset:0;clip-path:polygon(8% 0,100% 0,92% 100%,0 100%)}
.card .label{position:absolute;left:0;bottom:0;width:100%;height:21px;background:var(--blue-deep);clip-path:polygon(1.3% 0,98.7% 0,98% 100%,0 100%);color:var(--white);font-family:"Oswald",sans-serif;font-size:12px;text-align:center;line-height:21px}
/* about */
.about-title{left:563px;top:1982px;font-family:"Oswald",sans-serif;font-weight:500;font-size:40px;color:var(--white)}
.about-text{left:563px;top:2062px;width:530px;font-size:17.5px;line-height:21.5px;color:var(--white)}
/* gallery & video */
.tile{position:absolute}
.play{position:absolute;width:50px;height:50px;border-radius:50%;background:rgba(31,86,179,.9);display:flex;align-items:center;justify-content:center}
/* footer */
.foot-text{font-size:14px;line-height:18px;color:var(--white)}
.foot-head{font-family:"Montserrat",sans-serif;font-weight:600;font-size:20px;color:var(--white)}
.foot-link{position:absolute;left:532px;font-size:16px;color:var(--white)}
</style>
</head>
<body>
<div class="page">

  <!-- hero background -->
  <div class="abs hero-photo" role="img" aria-label="White luxury yacht cruising fast through rough blue ocean waves"></div>
  <svg class="abs" style="left:0;top:0" width="1200" height="700" aria-hidden="true">
    <rect x="0" y="0" width="1200" height="130" fill="#fff"/>
    <path d="M0 130 C300 150 700 120 1200 125 L1200 0 L0 0Z" fill="#fff"/>
    <path d="M0 662 L560 590 L520 690 L0 690Z" fill="#1f56b3"/>
    <path d="M0 668 L540 600 C700 650 900 690 1200 664 L1200 700 L0 700Z" fill="#fff"/>
  </svg>

  <!-- nav -->
  <div class="abs brand">GARLAND<span class="brand-sub">CUSTOM BOATS</span></div>
  <nav class="abs nav">
    <span style="left:0">HOME</span>
    <span style="left:78px">ABOUT</span>
    <span style="left:158px">BOATS</span>
    <span style="left:242px">WHY CHOOSE US</span>
    <span style="left:392px">BLOG</span>
  </nav>
  <div class="btn" style="left:941px;top:42px;width:167px;height:38px;font-size:12px">Get in touch</div>

  <!-- hero content -->
  <div class="abs hero-circle"></div>
  <h1 class="abs hero-title">BUILDING CUSTOM<br>BOATS SINCE 1982</h1>
  <p class="abs hero-text">We specialize in Dive Boats, Yacht Sport Fisherman, Patrol Boats, and Research Vessels.</p>
  <div class="btn" style="left:205px;top:438px;width:168px;height:38px;font-size:12px">Get in touch</div>

  <!-- why choose us -->
  <h2 class="abs heading" style="top:762px;left:22px">Why Choose Us</h2>

  <div class="feature" style="left:100px">
    <svg width="96" height="92" viewBox="0 0 96 92" fill="none" stroke="#1f56b3" stroke-width="3">
      <path d="M40 8 L48 8 L50 18 L58 22 L66 16 L72 22 L66 30 L70 38 L80 40 L80 50 L70 52 L66 60 L72 68 L66 74 L58 68 L50 72 L48 82 L40 82 L38 72 L30 68 L22 74 L16 68 L22 60 L18 52 L8 50 L8 40 L18 38 L22 30 L16 22 L22 16 L30 22 L38 18Z"/>
      <path d="M44 32 L44 60"/><path d="M44 36 L70 36 M44 46 L88 46 M44 56 L70 56"/>
      <circle cx="74" cy="36" r="3"/><circle cx="91" cy="46" r="3"/><circle cx="74" cy="56" r="3"/>
    </svg>
    <h3>Latest<br>Technologies</h3>
    <p>Garland Boats uses the latest technology and only the highest quality materials to build our custom boats.</p>
  </div>

  <div class="feature" style="left:452px">
    <svg width="110" height="92" viewBox="0 0 110 92" fill="none" stroke="#1f56b3" stroke-width="3">
      <path d="M14 56 L96 56 L84 72 L22 72Z"/>
      <path d="M30 56 L38 40 L72 40 L80 56"/><path d="M44 40 L48 30 L66 30 L68 40"/>
      <path d="M6 82 C18 76 26 88 38 82 C50 76 58 88 70 82 C82 76 90 88 104 82"/>
    </svg>
    <h3>High<br>Quality</h3>
    <p>Our ongoing commitment to quality and customer satisfaction have helped us establish our position as a leader in custom boat industry.</p>
  </div>

  <div class="feature" style="left:803px">
    <svg width="96" height="92" viewBox="0 0 96 92" fill="none" stroke="#1f56b3" stroke-width="3">
      <circle cx="52" cy="28" r="18"/><path d="M44 28 L50 34 L60 22"/>
      <path d="M42 44 L38 58 M62 44 L66 58"/>
      <path d="M8 62 L24 56 L48 62 C54 64 54 70 48 70 L34 70 M24 82 L58 82 L84 62 C88 58 84 54 80 56 L62 66"/>
    </svg>
    <h3>Commitment to<br>Excellence</h3>
    <p>We believe the commitment is essential for our continued success and growth. Our company provides quality custom boats that exceed our customers expectations.</p>
  </div>

  <!-- latest inventory -->
  <h2 class="abs heading" style="top:1215px;left:17px">Latest Inventory</h2>
  <svg class="abs" style="left:36px;top:1422px" width="20" height="26" aria-hidden="true"><path d="M14 3 L5 13 L14 23" stroke="#1f56b3" stroke-width="3" fill="none"/></svg>
  <svg class="abs" style="left:1125px;top:1466px" width="20" height="26" aria-hidden="true"><path d="M6 3 L15 13 L6 23" stroke="#1f56b3" stroke-width="3" fill="none"/></svg>

  <div class="card" style="left:93px">
    <div class="shot" role="img" aria-label="White custom dive boat on the water" style="background:linear-gradient(180deg,#8fb3d3,#e9eef2 55%,#4f7fa0)"></div>
    <div class="label">Custom Dive</div>
  </div>
  <div class="card" style="left:350px">
    <div class="shot" role="img" aria-label="Sport fish boat on green water" style="background:linear-gradient(180deg,#6fa6d8,#dfe7ec 50%,#1f8f7a)"></div>
    <div class="label">Sport Fish</div>
  </div>
  <div class="card" style="left:605px">
    <div class="shot" role="img" aria-label="Research vessel docked by a marsh" style="background:linear-gradient(180deg,#9eb7cc,#c9cfc9 50%,#6a7e84)"></div>
    <div class="label">Research Vessel</div>
  </div>
  <div class="card" style="left:862px">
    <div class="shot" role="img" aria-label="Glass bottom boat with open deck railings" style="background:linear-gradient(180deg,#d8dde0,#eef0f0 45%,#2f3a3d)"></div>
    <div class="label">Glass Bottom</div>
  </div>

  <div class="btn" style="left:539px;top:1659px;width:131px;height:28px;font-size:10px">View all boats</div>

  <!-- about -->
  <svg class="abs" style="left:0;top:1785px" width="1200" height="665" aria-hidden="true">
    <path d="M0 101 L600 3 L1200 101 L1200 595 L600 661 L0 595Z" fill="#1f56b3"/>
  </svg>
  <div class="abs" role="img" aria-label="Faint photo of a boat on the water behind the about section" style="left:420px;top:2160px;width:380px;height:220px;background:radial-gradient(ellipse at center,rgba(255,255,255,.1),rgba(255,255,255,0) 70%)"></div>
  <div class="abs" style="left:82px;top:1937px;width:414px;height:414px;border-radius:50%;background:#7d9fd6"></div>
  <div class="abs" role="img" aria-label="White motor yacht with flybridge" style="left:98px;top:2005px;width:402px;height:230px;border-radius:40% 40% 30% 30%;background:linear-gradient(180deg,#e9eef4,#c3cdd9 60%,#8a9ab0)"></div>
  <h2 class="abs about-title">ABOUT GARLAND BOATS</h2>
  <p class="abs about-text">Our Garland Dive Specials are especially designed for dive operators and dive enthusiasts alike. From our custom dive tank holders, water entry platforms, camera tables, fresh water rinse-downs, ample deck space and much, much more, you will see why our dive boats are making waves in the dive industry and are the number one requested boats by both divers and charter operators!</p>
  <div class="btn" style="left:563px;top:2249px;width:133px;height:27px;font-size:10px">View all boats</div>

  <!-- gallery -->
  <h2 class="abs heading" style="top:2560px;left:5px">Our Gallery</h2>
  <div class="tile" role="img" aria-label="Dive boat with divers aboard on turquoise water" style="left:119px;top:2677px;width:268px;height:167px;background:linear-gradient(180deg,#2f8ccc,#e6edf0 55%,#1e8fb0)"></div>
  <div class="tile" role="img" aria-label="White boat moored by a tree-lined shore" style="left:119px;top:2856px;width:268px;height:166px;background:linear-gradient(180deg,#b6c9d8,#5f7d52 40%,#d9dfe2 60%,#56646c)"></div>
  <div class="tile" role="img" aria-label="Custom boat with canopy heading toward the camera on grey water" style="left:406px;top:2677px;width:387px;height:345px;background:linear-gradient(180deg,#d7dadb,#e8ebea 45%,#8f9a9a)"></div>
  <div class="tile" role="img" aria-label="Boat speeding across golden water leaving a wake" style="left:814px;top:2677px;width:267px;height:167px;background:linear-gradient(150deg,#7e8c86,#c7b38a 60%,#3c5e6a)"></div>
  <div class="tile" role="img" aria-label="Dive boat flying a dive flag near a harbour" style="left:814px;top:2856px;width:267px;height:166px;background:linear-gradient(180deg,#8fb7dc,#e3e8ea 55%,#3a7ca3)"></div>

  <!-- videos -->
  <h2 class="abs heading" style="top:3185px;left:7px">Latest Videos</h2>
  <div class="tile" role="img" aria-label="Video still of a boat cruising past a waterfront" style="left:121px;top:3281px;width:395px;height:189px;background:linear-gradient(180deg,#9fb0bc,#6c7c6e 45%,#5b6d7a)"></div>
  <div class="tile" role="img" aria-label="Video still of a canopy boat on calm water" style="left:121px;top:3514px;width:395px;height:191px;background:linear-gradient(180deg,#b5bec2,#8d9a93 55%,#6f7f86)"></div>
  <div class="tile" role="img" aria-label="Video still of a boat at a dock at dusk" style="left:555px;top:3281px;width:521px;height:424px;background:linear-gradient(180deg,#9aa7b4,#5d6a62 45%,#2c3840)"></div>
  <div class="play" style="left:289px;top:3337px"><svg width="20" height="22"><path d="M3 1 L19 11 L3 21Z" fill="#fff"/></svg></div>
  <div class="play" style="left:289px;top:3582px"><svg width="20" height="22"><path d="M3 1 L19 11 L3 21Z" fill="#fff"/></svg></div>
  <div class="play" style="left:790px;top:3467px"><svg width="20" height="22"><path d="M3 1 L19 11 L3 21Z" fill="#fff"/></svg></div>
  <div class="btn" style="left:509px;top:3761px;width:160px;height:34px;font-size:11px">View all videos</div>

  <!-- footer -->
  <svg class="abs" style="left:0;top:3930px" width="1200" height="574" aria-hidden="true">
    <path d="M0 127 L600 16 L1200 127 L1200 574 L0 574Z" fill="#2b2c2f"/>
    <path d="M0 127 L600 16 L1200 127 L1200 120 L600 8 L0 120Z" fill="#1f56b3"/>
    <path d="M0 127 L600 20 L600 36 L0 137Z" fill="#1f56b3" opacity=".6"/>
  </svg>
  <div class="abs" role="img" aria-label="Faint boat silhouette behind the footer content" style="left:640px;top:4240px;width:560px;height:264px;background:linear-gradient(180deg,rgba(43,44,47,0),#25262a)"></div>
  <div class="abs" style="left:530px;top:3885px;width:134px;height:134px;border-radius:50%;background:#1f56b3;border:4px solid #fff"></div>

  <div class="abs brand" style="left:88px;top:4160px;font-size:30px">GARLAND</div>
  <p class="abs foot-text" style="left:86px;top:4244px;width:400px;font-size:13.5px">If you don't see what you are looking for....ASK.<br>We can customize your boat to suit your needs.</p>
  <p class="abs foot-text" style="left:86px;top:4300px;width:400px;font-size:13.5px">Make sure you check out our links for more<br>pictures of our boats in use!</p>

  <div class="abs foot-head" style="left:522px;top:4176px">QUICK LINKS</div>
  <div class="foot-link" style="top:4230px">HOME</div>
  <div class="foot-link" style="top:4274px">ABOUT US</div>
  <div class="foot-link" style="top:4318px">BOATS</div>
  <div class="foot-link" style="top:4362px">CONTACT US</div>

  <div class="abs foot-head" style="left:819px;top:4180px">CONTACT INFO</div>
  <p class="abs foot-text" style="left:827px;top:4236px;font-size:16px">ph: 555.014.2087</p>
  <p class="abs foot-text" style="left:827px;top:4282px;width:340px;font-size:16px;line-height:21px">Garland Boats, Inc. &nbsp; 4210 Harbor Rd.<br>Bayport, Louisiana &nbsp;70999</p>

  <p class="abs foot-text" style="left:88px;top:4464px;font-size:14px">All Boats are FOB Bayport, Louisiana &nbsp;USA</p>
  <p class="abs foot-text" style="left:843px;top:4464px;font-size:14px">Privacy Policy | Terms &amp; Conditions</p>

</div>
</body>
</html>
```